Company raising consciousness thru leadership & self-awareness needs amazing Letterhead

We are a technology company that spun out of a consulting firm. We are waking people up in corporate America through surveys, leadership development, workshops and consulting. Getting employees to become self-aware and changing company culture through improved leadership and team effectiveness. We need Word letterhead for our proposals, handouts, and worksheets that match our brand standard, is fresh, and communicates trust, credibility and professionalism.

Our target clients are other businesses, and executive leaders and C-suite leaders in those companies.

Sans Serif

• A Word template we can use for handouts, proposals, executive summary, project management documents, and letters. We need our logo. Please add page number and date on the footer. Must match the theme of our new website in look and feel to match the brand we are trying to promote. Use the colors from our brand standard document I submitted.

```html
<!DOCTYPE html>
<html lang="en">
<head>
<meta charset="utf-8">
<title>Corvane Leadership Letterhead</title>
<link href="https://fonts.googleapis.com/css2?family=Open+Sans:wght@400;600&family=Lato:wght@400&display=swap" rel="stylesheet">
<style>
  :root {
    --navy: #223a74;
    --purple: #7b35b3;
    --ink: #4a4a4a;
    --ink-strong: #333333;
    --paper: #ffffff;
    --backdrop: #e4e4e6;
  }
  * { margin: 0; padding: 0; box-sizing: border-box; }
  html, body { width: 1040px; height: 1200px; overflow: hidden; background: var(--backdrop); }
  .letterhead {
    position: absolute; left: 54px; top: 0;
    width: 932px; height: 1200px;
    background: var(--paper);
    font-family: "Open Sans", Arial, sans-serif;
    color: var(--ink);
    overflow: hidden;
  }
  .brand {
    position: absolute; right: 92px; top: 110px;
    display: flex; align-items: center; gap: 12px;
  }
  .brand-dot { width: 34px; height: 34px; border-radius: 50%; background: var(--navy); }
  .brand-name { font-size: 22px; font-weight: 600; color: var(--navy); letter-spacing: .5px; }
  .block { position: absolute; left: 87px; font-size: 15px; line-height: 18px; }
  .issue-date { top: 216px; }
  .recipient { top: 253px; }
  .salutation { top: 357px; }
  .body-copy { top: 408px; width: 753px; }
  .body-copy p { line-height: 27px; text-align: justify; margin-bottom: 27px; }
  .closing { top: 815px; }
  .signatory { top: 890px; }
  .signatory-name { font-size: 19px; color: var(--ink-strong); line-height: 24px; }
  .signatory-role { font-size: 15px; margin-top: 8px; }
  .footer { position: absolute; left: 0; bottom: 0; width: 932px; height: 165px; }
  .footer svg { position: absolute; inset: 0; }
  .footer-address, .footer-contact {
    position: absolute; color: #fff;
    font-family: "Lato", Arial, sans-serif; font-size: 17px;
  }
  .footer-address { left: 90px; top: 114px; }
  .footer-contact { right: 92px; top: 88px; text-align: right; line-height: 22px; }
  .contact-line { display: flex; justify-content: flex-end; align-items: center; gap: 4px; }
  .contact-line svg { position: static; width: 17px; height: 17px; }
</style>
</head>
<body>
<div class="letterhead">
  <div class="brand">
    <span class="brand-dot"></span>
    <span class="brand-name">Corvane Leadership</span>
  </div>

  <div class="block issue-date">Issuing Date: May 5, 2018</div>
  <div class="block recipient">Name Of Employee Mr. XYZABC<br>Address of Employee<br>Address Line 2 etc..</div>
  <div class="block salutation">Dear Mr.XYZABC</div>

  <div class="block body-copy">
    <p>Lorem Ipsum has been the industry's standard dummy text ever since the 1500s, when an unknown printer took a galley of type and scrambled it to make a type specimen book. It has survived not only five centuries, but also the leap into electronic typesetting, remaining essentially unchanged. It was popularised in the 1960s with the release of Letraset sheets containing Lorem Ipsum passages, and more recently with desktop publishing software like Aldus PageMaker including versions of Lorem Ipsum.</p>
    <p>Lorem Ipsum is simply dummy text of the printing and typesetting industry. Lorem Ipsum has been the industry's standard dummy text ever since the 1500s, when an unknown printer took a galley of type and scrambled it to make a type specimen book.</p>
    <p>It has survived not only five centuries, but also the leap into electronic typesetting, remaining essentially unchanged. It was popularised in the 1960s with the release of Letraset sheets containing Lorem IpsumIpsum passages.</p>
  </div>

  <div class="block closing">Yours Sincerely</div>
  <div class="block signatory">
    <div class="signatory-name">Marcus Hale</div>
    <div class="signatory-role">Managing Director</div>
  </div>

  <footer class="footer">
    <svg viewBox="0 0 932 165" width="932" height="165" preserveAspectRatio="none">
      <path d="M0,47 C160,92 320,98 490,80 C660,62 800,22 932,20 L932,165 L0,165 Z" fill="var(--navy)"/>
      <path d="M0,6 C110,52 290,76 560,40 C360,78 140,70 0,40 Z" fill="var(--purple)"/>
    </svg>
    <div class="footer-address">421, Address line here,&nbsp; 45452 Country Name</div>
    <div class="footer-contact">
      <div class="contact-line">044-555 010 234
        <svg viewBox="0 0 16 16"><path d="M3 2h3l1 3-2 1a8 8 0 0 0 5 5l1-2 3 1v3a2 2 0 0 1-2 2A12 12 0 0 1 1 4a2 2 0 0 1 2-2z" fill="#fff"/></svg>
      </div>
      <div class="contact-line">hello@corvane.com
        <svg viewBox="0 0 16 16"><rect x="1" y="3" width="14" height="10" fill="#fff"/><path d="M1 3l7 6 7-6" stroke="var(--navy)" stroke-width="1.3" fill="none"/></svg>
      </div>
      <div class="contact-line">www.corvane.com
        <svg viewBox="0 0 16 16"><circle cx="8" cy="8" r="7" fill="#fff"/><path d="M5 4l3 2-1 3 3 2" stroke="var(--navy)" stroke-width="1.5" fill="none"/></svg>
      </div>
    </div>
  </footer>
</div>
</body>
</html>
```